MCLS Banner

We need a design for a pull-up banner (850 x 2000 mm) to promote the Merida Cable Ledger Scheme. https://mclsnet.info/en/
The banner action should be to get people to scan a QR code to join a mailing list (add a frame to add the QR code)

Use the website colours and typology https://mclsnet.info/en/
See also brochure for ideas https://mclsnet.info/documents/9/MCLS_brochure_english.pdf

```html
<!DOCTYPE html>
<html lang="en">
<head>
<meta charset="utf-8">
<title>MCLS Banner</title>
<link rel="stylesheet" href="https://fonts.googleapis.com/css2?family=Montserrat:wght@500;700;800&family=Source+Sans+3:wght@400&display=swap">
<style>
  :root {
    --lime: #bccf34;
    --ink: #1c1a2e;
    --deep: #03101a;
    --night: #062234;
    --glow: #1a7fb0;
    --white: #ffffff;
  }
  * { margin: 0; padding: 0; box-sizing: border-box; }
  html, body { width: 1200px; height: 2820px; overflow: hidden; background: var(--white); }
  .banner { position: relative; width: 1200px; height: 2820px; background: var(--white); }
  .brand {
    position: absolute; left: 168px; top: 180px;
    font-family: "Montserrat", sans-serif; font-weight: 700;
    font-size: 190px; line-height: 1; letter-spacing: -4px;
    color: var(--ink);
  }
  .hero {
    position: absolute; left: 0; top: 578px; width: 1200px; height: 2101px;
    background:
      radial-gradient(ellipse 520px 380px at 860px 420px, rgba(60,190,240,.55), transparent 70%),
      radial-gradient(ellipse 420px 320px at 360px 520px, rgba(40,150,210,.45), transparent 70%),
      radial-gradient(ellipse 180px 700px at 840px 1100px, rgba(40,170,220,.35), transparent 70%),
      radial-gradient(ellipse 160px 620px at 840px 1700px, rgba(30,30,34,.85), transparent 70%),
      linear-gradient(180deg, var(--night) 0%, #0a2c40 35%, var(--deep) 75%, #02080e 100%);
  }
  .headline {
    position: absolute; left: 159px; top: 1592px;
    font-family: "Montserrat", sans-serif; font-weight: 700;
    font-size: 78px; line-height: 88px; letter-spacing: -1.5px;
    color: var(--lime);
  }
  .rule {
    position: absolute; left: 147px; top: 1876px; width: 534px; height: 4px;
    background: var(--white);
  }
  .standard {
    position: absolute; left: 147px; top: 1902px;
    font-family: "Source Sans 3", sans-serif; font-weight: 400;
    font-size: 42px; line-height: 52px; color: var(--lime);
  }
  .cta-title {
    position: absolute; left: 141px; top: 2030px;
    font-family: "Montserrat", sans-serif; font-weight: 800;
    font-size: 49px; line-height: 61px; letter-spacing: -1px;
    color: var(--lime); text-transform: uppercase;
  }
  .cta-text {
    position: absolute; left: 141px; top: 2170px;
    font-family: "Source Sans 3", sans-serif; font-weight: 400;
    font-size: 41px; line-height: 54px; color: var(--white);
  }
  .qr-frame {
    position: absolute; left: 138px; top: 2358px; width: 346px; height: 321px;
    background: var(--lime);
  }
  .footer {
    position: absolute; left: 0; top: 2679px; width: 1200px; height: 141px;
    background: var(--lime);
    display: flex; align-items: center; padding-left: 140px;
    font-family: "Source Sans 3", sans-serif; font-weight: 400;
    font-size: 37px; color: var(--ink);
  }
  .footer .sep { margin: 0 38px; }
</style>
</head>
<body>
<div class="banner">
  <div class="brand">mcls</div>

  <div class="hero" role="img" aria-label="Glowing world map with connected network nodes and light beams converging into a black fibre cable connector"></div>

  <h1 class="headline">Mapping the<br>world's Internet<br>backbone.</h1>
  <div class="rule"></div>
  <p class="standard">Merida Cable Ledger Scheme</p>

  <h2 class="cta-title">Join the<br>MCLS mailing list</h2>
  <p class="cta-text">To stay up to date with and<br>contribute to the development<br>and adoption of MCLS.</p>

  <div class="qr-frame"></div>

  <footer class="footer">
    <span class="web">www.mclsnet.info</span>
    <span class="sep">|</span>
    <span class="mail">outreach@mclsnet.info</span>
  </footer>
</div>
</body>
</html>
```